Website for legal expungement services with button to qualify/disqualify potential clients

Brightpath Record Renewal, LLC is a law firm focusing in legal expungement servcies (allowing people to erase criminal court records, police records, proseution files, etc). I want a more modern look which exudes confidence in the services. I am looking for a clean website that looks very polished. I want to keep the pages to a minimum, as I want the page not so much to answer questions, but to direct traffic to contact the law office. I would like the main focus point to be an button which would take a client through a series of questions to see if they would qualify for the services; this serves two purposes 1) to collect contact info for future marketing via email and 2) eliminate individuals who we are currently unable to help. A current theme that I have played around with are "Change so much, you'll need to reintroduce yourself" alongside a picture of a guys hand outstretched.
On the landing page, I would like a very brief and to the point explanation of what the service would be (i.e. "Leave your past in the past; expunge all your criminal records" ), followed by a list of benefits that it provides. (NB: included is a file "law post card-02" that includes the main benefits to expungement). Also included are two logo files for a more updated logo I currently use ("BRR Logo" and BRR Logo2") (NB: I'm open to revisions on this as well). Lastly, I've had two very minor 'ads' that I did ("postcard back" and "KVT Ad") that I like the idea of.

Target Market(s)

Middle/upper-middle class, mostly male, people with a criminal record or criminal accusation

Industry/Entity Type

Legal Services

Coding

Coded - Design and coding required

Requirements
Must have
• Button that attracts attention up front (possibly stand out coloring) to click to open up a series of questions to qualify/eliminate prospects, and simultaneously gather their info. Also, must be mobile friendly.

```html
<!DOCTYPE html>
<html lang="en">
<head>
<meta charset="utf-8">
<title>Brightpath Record Renewal</title>
<link href="https://fonts.googleapis.com/css2?family=Cinzel:wght@600;700&family=Open+Sans:wght@400;600;700&display=swap" rel="stylesheet">
<style>
:root{
  --navy:#0b3a76;
  --navy-deep:#08305f;
  --ink:#1c1c1c;
  --white:#ffffff;
  --gold-1:#f3d34a;
  --gold-2:#c89a0c;
  --footer:#1d1f22;
  --muted:#e9edf3;
}
*{box-sizing:border-box;margin:0;padding:0}
html,body{width:1200px;height:3237px;overflow:hidden}
body{position:relative;font-family:"Open Sans",Arial,sans-serif;background:var(--white);color:var(--ink)}
.abs{position:absolute}
.serif{font-family:"Cinzel",Georgia,serif}

/* hero */
.hero{left:0;top:0;width:1200px;height:686px;background:radial-gradient(ellipse at 50% 40%,#4c5866 0%,#2c343e 55%,#1a1f26 100%)}
.hero-photo{left:0;top:0;width:1200px;height:686px;background:linear-gradient(180deg,rgba(30,50,80,.35),rgba(20,25,35,.15) 60%,rgba(20,25,35,.4))}
.brand-box{left:112px;top:34px;width:92px;height:34px;border:2px solid var(--white);color:var(--white);font-size:22px;letter-spacing:6px;text-align:center;line-height:30px;font-family:"Open Sans",Arial,sans-serif}
.brand-rule{left:231px;top:14px;width:1px;height:70px;background:rgba(255,255,255,.7)}
.brand-name{left:260px;top:33px;color:var(--white);font-family:"Cinzel",Georgia,serif;font-size:14px;line-height:17px;letter-spacing:.5px;font-weight:600}
.nav-tab{left:493px;top:0;width:62px;height:98px}
.nav a{position:absolute;top:42px;color:var(--white);font-size:13px;font-weight:700;text-decoration:none}
.quote{left:952px;top:31px;width:136px;height:41px;border:2px solid var(--white);color:var(--white);font-size:12px;font-weight:700;text-align:center;line-height:37px}
.headline{left:0;top:240px;width:1200px;text-align:center;color:var(--white);font-size:52px;line-height:53px;font-weight:700}
.book{left:415px;top:362px;width:370px;height:69px;background:linear-gradient(180deg,var(--gold-1),var(--gold-2));color:var(--white);font-size:22px;font-weight:700;text-align:center;line-height:69px}
.arrow{top:618px;width:29px;height:29px;background:var(--white)}

/* titles */
.section-title{left:0;width:1200px;text-align:center;font-family:"Cinzel",Georgia,serif;font-weight:700;font-size:44px;color:var(--navy)}

/* services */
.svc{top:856px;width:466px;height:296px;border:3px solid #111;background:var(--white)}
.svc-title{position:absolute;top:17px;font-family:"Cinzel",Georgia,serif;font-size:19px;color:var(--navy);font-weight:600;white-space:nowrap}
.svc-pic{top:911px;height:241px}
.svc-label{left:171px;top:922px;color:var(--white);font-family:"Open Sans",Arial,sans-serif;font-weight:700;font-size:18px;line-height:25px}

/* benefits */
.benefits{left:0;top:1257px;width:1200px;height:732px;background:var(--navy)}
.benefits .section-title{color:var(--white);top:75px}
.benefit-photo{left:423px;top:170px;width:355px;height:473px;background:linear-gradient(180deg,#a9a49c,#6d6a68 45%,#3d3f45)}
.benefit{width:220px;color:var(--white);font-size:12.5px;font-weight:700;line-height:21px}
.benefit.left{left:72px;text-align:right}
.benefit.right{left:897px}

/* cases */
.case-pic{top:2174px;width:308px;height:329px}
.case-label{top:2457px;width:275px;height:95px;background:var(--white);border:1px solid #d9dde3;text-align:center;font-size:17px;font-weight:600;color:#2b2b2b;line-height:26px;padding-top:21px}

/* footer */
.footer-bg{left:0;top:2705px;width:1200px;height:532px;background:linear-gradient(180deg,#25282c,#15171a)}
.footer-title{position:absolute;top:2792px;color:var(--white);font-size:22px;font-weight:700;line-height:30px}
.links li,.contacts li{list-style:none;color:var(--white);font-size:15px;position:absolute}
.copy{left:112px;top:3060px;color:var(--white);font-size:15px}
.social{top:3097px;width:30px;height:30px;border-radius:50%;border:1px solid rgba(255,255,255,.55)}
.social::after{content:"";position:absolute;left:10px;top:10px;width:8px;height:8px;background:var(--white)}
.field{left:627px;width:433px;border:2px solid var(--white);color:var(--white);font-size:14px;padding:10px 24px}
.submit{left:627px;top:3023px;width:433px;height:52px;background:var(--white);color:var(--navy);font-size:13px;font-weight:700;text-align:center;line-height:52px}
</style>
</head>
<body>

<header>
  <div class="abs hero"></div>
  <div class="abs hero-photo" role="img" aria-label="Man in a navy suit holding out an open hand"></div>

  <div class="abs brand-box">BRR</div>
  <div class="abs brand-rule"></div>
  <div class="abs brand-name">BRIGHTPATH RECORD<br>RENEWAL</div>

  <svg class="abs nav-tab" viewBox="0 0 62 98" aria-hidden="true"><path d="M0 0H62V82L31 98L0 82Z" fill="#0b3a76"/></svg>
  <nav class="nav">
    <a style="left:505px">Home</a>
    <a style="left:570px">About</a>
    <a style="left:636px">Service</a>
    <a style="left:709px">Benefits</a>
    <a style="left:789px">Reviews</a>
    <a style="left:867px">Contact</a>
  </nav>
  <div class="abs quote">GET A QUOTE</div>

  <h1 class="abs headline serif">Change so much, you'll need to<br>reintroduce yourself</h1>
  <div class="abs book">BOOK AN APPOINTMENT</div>

  <svg class="abs arrow" style="left:562px" viewBox="0 0 29 29" aria-label="Previous slide"><path d="M16 10L12 14.5L16 19" stroke="#333" stroke-width="1.5" fill="none"/></svg>
  <svg class="abs arrow" style="left:604px" viewBox="0 0 29 29" aria-label="Next slide"><path d="M13 10L17 14.5L13 19" stroke="#333" stroke-width="1.5" fill="none"/></svg>
</header>

<section class="services">
  <h2 class="abs section-title" style="top:778px">OUR SERVICES</h2>
  <div class="abs svc" style="left:112px"><h3 class="svc-title" style="right:24px">LEAVE YOUR PAST IN THE PAST</h3></div>
  <div class="abs svc-pic" style="left:161px;width:416px;background:linear-gradient(135deg,#4a3526,#7a6a5c 50%,#cfd0d6)" role="img" aria-label="Woman signing documents at a desk"></div>
  <div class="abs svc-label">Expungement<br>Attorneys</div>

  <div class="abs svc" style="left:622px"><h3 class="svc-title" style="left:32px">EXPUNGE ALL YOUR CRIMINAL RECORDS</h3></div>
  <div class="abs svc-pic" style="left:622px;width:417px;background:linear-gradient(135deg,#1f2836,#3c4c62 55%,#7f9cbb)" role="img" aria-label="Hand holding floating legal icons"></div>
</section>

<section class="abs benefits">
  <h2 class="abs section-title">BENEFITS OF EXPUNGING</h2>
  <div class="abs benefit-photo" role="img" aria-label="Smiling attorney in a grey suit with arms crossed"></div>

  <p class="abs benefit left" style="top:183px">Lorem ipsum dolor sit amet,<br>consectetur adipiscing</p>
  <p class="abs benefit left" style="top:317px">Lorem ipsum dolor sit amet,<br>consectetur adipiscing</p>
  <p class="abs benefit left" style="top:451px">Lorem ipsum dolor sit amet,<br>consectetur adipiscing</p>
  <p class="abs benefit left" style="top:586px">Lorem ipsum dolor sit amet,<br>consectetur adipiscing</p>
  <p class="abs benefit right" style="top:183px">Lorem ipsum dolor sit amet,<br>consectetur adipiscing</p>
  <p class="abs benefit right" style="top:317px">Lorem ipsum dolor sit amet,<br>consectetur adipiscing</p>
  <p class="abs benefit right" style="top:451px">Lorem ipsum dolor sit amet,<br>consectetur adipiscing</p>
  <p class="abs benefit right" style="top:586px">Lorem ipsum dolor sit amet,<br>consectetur adipiscing</p>

  <svg class="abs" style="left:0;top:0" width="1200" height="732" aria-hidden="true">
    <g fill="#fff" stroke="#0b3a76" stroke-width="1.3">
      <circle cx="343" cy="206" r="34"/><circle cx="343" cy="340" r="34"/><circle cx="343" cy="474" r="34"/><circle cx="343" cy="609" r="34"/>
      <circle cx="849" cy="206" r="34"/><circle cx="849" cy="340" r="34"/><circle cx="849" cy="474" r="34"/><circle cx="849" cy="609" r="34"/>
    </g>
    <g fill="none" stroke="#0b3a76" stroke-width="1.6">
      <circle cx="343" cy="198" r="9"/><path d="M325 214h14l8 5h12"/>
      <path d="M330 333h20a7 7 0 0 1 0 14h-14"/>
      <path d="M343 458l13 5v10c0 9-6 14-13 17c-7-3-13-8-13-17v-10z"/><rect x="338" y="470" width="10" height="8"/>
      <rect x="332" y="594" width="22" height="28"/><path d="M336 602h14M336 608h14M336 614h10"/>
      <path d="M840 198l10 10M846 192l10 10M848 200l-10 10M836 220h20"/>
      <path d="M834 340l15-13l15 13v14h-30z"/><rect x="845" y="345" width="8" height="9"/>
      <path d="M840 460h18v8a9 9 0 0 1-18 0zM849 477v8M842 488h14"/>
      <circle cx="849" cy="605" r="10"/><path d="M835 620h28"/>
    </g>
  </svg>
</section>

<section class="cases">
  <h2 class="abs section-title" style="top:2084px">WHAT TYPES OF CASES QUALITY</h2>
  <div class="abs case-pic" style="left:112px;background:linear-gradient(135deg,#2a1d17,#6b4a3a 50%,#c9572a)" role="img" aria-label="Lawyer meeting a client in an orange prison uniform"></div>
  <div class="abs case-pic" style="left:446px;background:linear-gradient(135deg,#1b1713,#5a4a3c 55%,#b7ad9d)" role="img" aria-label="Handcuffed hands resting on an open law book"></div>
  <div class="abs case-pic" style="left:780px;background:linear-gradient(135deg,#7a7f82,#c9c3b8 55%,#e5ded3)" role="img" aria-label="Woman reviewing a document across a desk"></div>
  <div class="abs case-label" style="left:128px">Criminal accusations that<br>were dismissed</div>
  <div class="abs case-label" style="left:463px">Criminal cases that went<br>into a diversionary</div>
  <div class="abs case-label" style="left:797px">Convictions</div>
</section>

<footer>
  <div class="abs footer-bg" role="img" aria-label="Dark city skyline at night"></div>
  <svg class="abs" style="left:572px;top:2655px" width="30" height="52" aria-hidden="true"><path d="M27 0V52H0L12 20Z" fill="#3a3c40"/></svg>
  <svg class="abs" style="left:599px;top:2655px" width="489" height="530" aria-hidden="true"><path d="M0 0H489V474L244 530L0 474Z" fill="#0b3a76"/></svg>

  <h4 class="footer-title" style="left:112px">Quick Links</h4>
  <ul class="links">
    <li style="left:112px;top:2841px">»&nbsp;&nbsp;&nbsp;&nbsp;Home</li>
    <li style="left:112px;top:2867px">»&nbsp;&nbsp;&nbsp;&nbsp;About</li>
    <li style="left:112px;top:2893px">»&nbsp;&nbsp;&nbsp;&nbsp;Service</li>
    <li style="left:112px;top:2918px">»&nbsp;&nbsp;&nbsp;&nbsp;Benifits</li>
    <li style="left:112px;top:2944px">»&nbsp;&nbsp;&nbsp;&nbsp;Blog</li>
    <li style="left:112px;top:2970px">»&nbsp;&nbsp;&nbsp;&nbsp;Contact</li>
  </ul>

  <h4 class="footer-title" style="left:327px">Contact Us</h4>
  <svg class="abs" style="left:325px;top:2843px" width="14" height="160" aria-hidden="true" fill="#fff">
    <path d="M7 0a5 5 0 0 1 5 5c0 4-5 9-5 9s-5-5-5-9a5 5 0 0 1 5-5zm0 3a2 2 0 1 0 0 4a2 2 0 0 0 0-4z"/>
    <path d="M2 76c1-2 3-2 4 0l1 2c0 1-1 2-1 2c1 2 3 4 5 5c0 0 1-1 2-1l2 1c2 1 2 3 0 4c-5 2-14-7-13-13z"/>
    <path d="M0 128h14v10H0zM0 128l7 6l7-6" stroke="#1d1f22" stroke-width="1"/>
  </svg>
  <ul class="contacts">
    <li style="left:354px;top:2841px;line-height:26px">Lorem ipsum dolor sit<br>amet</li>
    <li style="left:354px;top:2918px">555-014-2290</li>
    <li style="left:354px;top:2970px">hello@brightpathrenewal.com</li>
  </ul>

  <p class="abs copy">© Copyrights 2023 &nbsp;|&nbsp;All Rights Reserved</p>
  <div class="abs social" style="left:112px" aria-label="Social link"></div>
  <div class="abs social" style="left:152px" aria-label="Social link"></div>
  <div class="abs social" style="left:194px" aria-label="Social link"></div>
  <div class="abs social" style="left:236px" aria-label="Social link"></div>

  <div class="abs field" style="top:2688px;height:50px">Name</div>
  <div class="abs field" style="top:2748px;height:50px">Email address</div>
  <div class="abs field" style="top:2808px;height:50px">Phone</div>
  <div class="abs field" style="top:2867px;height:145px">Message</div>
  <div class="abs submit">SUBMIT NOW</div>
</footer>

</body>
</html>
```